Business Card Design & Gift cards, Gift Cert, Donation Card

Retail Gift Store-in addition to Business Cards we'd like sequenced 2 sided Gift cards, Gift Certificate Cards, and Donation Cards.please see examples and email for clarificationlogos attached with examples-
Gift Card, Gift Certificate and Donation Card will all be same style just differant upper right title, with back side info as example.
business card, as example is single sided.
looking for additional ideas for layout

Industry/Entity Type

Business

Contact Information for Business Card

211 Newman St.East Tawas, MI 48730989.362.8730Office@BrewKrew.com

Requirements
Must have
• Blue as per example
• Logos provided
• like gradiant background

```html
<!DOCTYPE html>
<html lang="en">
<head>
<meta charset="utf-8">
<title>Tillow Marsh – Business Card &amp; Gift Card</title>
<link rel="stylesheet" href="https://fonts.googleapis.com/css2?family=Delius&display=swap">
<style>
  :root {
    --page: #e9e6e1;
    --ink: #0a0a0a;
    --paper-white: #ffffff;
    --sky-light: #b3e0f7;
    --sky-mid: #8fcaf6;
    --sky-deep: #6fb4f5;
    --frame-line: #a9d6ef;
    --art-warm: #e86a5a;
    --art-sun: #f4df6a;
  }
  * { box-sizing: border-box; margin: 0; padding: 0; }
  html, body {
    width: 1200px;
    height: 892px;
    overflow: hidden;
    background: var(--page);
    font-family: "Delius", "Comic Sans MS", cursive;
  }
  .sheet {
    position: relative;
    width: 1200px;
    height: 892px;
  }

  /* Business card (portrait, single sided) */
  .business-card {
    position: absolute;
    left: 90px;
    top: 146px;
    width: 380px;
    height: 600px;
    background: var(--ink);
    padding: 14px;
    box-shadow: 0 10px 24px rgba(0,0,0,0.18);
  }
  .business-card__inner {
    position: relative;
    width: 100%;
    height: 100%;
    border: 5px solid var(--frame-line);
    background: linear-gradient(160deg, var(--sky-deep) 0%, var(--sky-mid) 45%, var(--sky-light) 100%);
    display: flex;
    flex-direction: column;
  }
  .business-card__brand {
    flex: 0 0 auto;
    padding-top: 28px;
    text-align: center;
  }
  .brand-name {
    color: var(--ink);
    font-size: 38px;
    font-weight: 400;
    letter-spacing: 1px;
    line-height: 1.05;
    text-transform: uppercase;
    white-space: nowrap;
  }
  .brand-art {
    width: 230px;
    height: 215px;
    margin: 18px auto 0;
    border-radius: 6px;
    background: linear-gradient(180deg, var(--art-warm) 0%, var(--art-warm) 55%, var(--art-sun) 100%);
    opacity: 0.85;
  }
  .business-card__contact {
    margin-top: auto;
    height: 250px;
    background: var(--ink);
    color: var(--paper-white);
    display: flex;
    flex-direction: column;
    justify-content: center;
    align-items: center;
    gap: 6px;
    font-size: 21px;
    letter-spacing: 1px;
    text-align: center;
  }

  /* Gift card (landscape, front) */
  .gift-card {
    position: absolute;
    left: 530px;
    top: 286px;
    width: 600px;
    height: 340px;
    background: linear-gradient(200deg, var(--sky-deep) 0%, var(--sky-mid) 45%, var(--sky-light) 100%);
    box-shadow: 0 10px 24px rgba(0,0,0,0.18);
    display: flex;
    flex-direction: column;
    justify-content: center;
    padding-left: 60px;
  }
  .gift-card__name {
    color: var(--ink);
    font-size: 60px;
    font-weight: 400;
    letter-spacing: 2px;
    text-transform: uppercase;
    line-height: 1;
    white-space: nowrap;
  }
  .gift-card__title {
    margin-top: 26px;
    color: var(--ink);
    font-size: 28px;
    letter-spacing: 1px;
  }
</style>
</head>
<body>
<main class="sheet">

  <article class="business-card">
    <div class="business-card__inner">
      <header class="business-card__brand">
        <h1 class="brand-name">Tillow Marsh</h1>
        <div class="brand-art" role="img" aria-label="Illustration area: a cheerful figure striding over a rising sun"></div>
      </header>
      <section class="business-card__contact">
        <p class="contact-phone">989.517.4296</p>
        <p class="contact-email">Office@TillowMarsh.com</p>
        <p class="contact-street">482 Larkfield Ave.</p>
        <p class="contact-city">Harlow Bay, MI 48291</p>
      </section>
    </div>
  </article>

  <article class="gift-card">
    <h2 class="gift-card__name">Tillow Marsh</h2>
    <p class="gift-card__title">gift card, gift certificate</p>
  </article>

</main>
</body>
</html>
```